BrindleStaffing Business Card Design

We are a staffing company finding positions for dedicated nurses and physicians.

Target Market(s)

Business Professionals

Industry/Entity Type

Staffing

Contact Information for Business Card

Gordon Pratley
Chairman
417 39th Avenue South
SAINT PETERSBURG FL 33712
813-555-4172 Mobile
813-555-8036 Fax
gpratley@brindlestaffing.com
www.brindlestaffing.com

Font styles to use
Sans Serif

Colors
fbee3e
f04a50
f37122

Requirements
Must have
• Logo Attached, see colors below. We'd like to see Yellow, Orange and Red.

```html
<!DOCTYPE html>
<html lang="en">
<head>
<meta charset="utf-8">
<title>BrindleStaffing Business Card</title>
<link href="https://fonts.googleapis.com/css2?family=Roboto:wght@400;500;700&display=swap" rel="stylesheet">
<style>
  :root {
    --backdrop: #e6e6e6;
    --brand-orange: #f37122;
    --brand-red: #f04a50;
    --brand-yellow: #fbee3e;
    --paper: #ffffff;
    --ink-light: #ffffff;
  }
  html, body {
    margin: 0;
    padding: 0;
    width: 1125px;
    height: 1200px;
    overflow: hidden;
    background: var(--backdrop);
    font-family: "Roboto", Arial, sans-serif;
  }
  .card {
    position: absolute;
    left: 150px;
    width: 825px;
    height: 470px;
    border-radius: 30px;
    overflow: hidden;
    background: var(--brand-orange);
  }
  .card--front { top: 99px; }
  .card--back { top: 631px; }
  .card__shape {
    position: absolute;
    inset: 0;
    width: 100%;
    height: 100%;
  }
  .wordmark {
    position: absolute;
    margin: 0;
    font-weight: 700;
    letter-spacing: -0.5px;
    white-space: nowrap;
    transform: translate(-50%, -50%);
  }
  .card--front .wordmark {
    left: 218px;
    top: 238px;
    font-size: 51px;
    color: var(--brand-red);
  }
  .card--back .wordmark {
    left: 408px;
    top: 250px;
    font-size: 80px;
    color: var(--ink-light);
  }
  .person {
    position: absolute;
    right: 36px;
    top: 56px;
    text-align: right;
    color: var(--ink-light);
  }
  .person__name {
    margin: 0;
    font-size: 29px;
    font-weight: 700;
    line-height: 1.15;
  }
  .person__title {
    margin: 0;
    font-size: 19px;
    font-weight: 500;
    line-height: 1.1;
  }
  .address {
    position: absolute;
    right: 36px;
    top: 249px;
    margin: 0;
    text-align: right;
    font-style: normal;
    font-size: 19px;
    line-height: 26px;
    color: var(--ink-light);
  }
  .contacts {
    position: absolute;
    right: 36px;
    top: 312px;
    margin: 0;
    padding: 0;
    list-style: none;
    text-align: right;
    font-size: 19px;
    line-height: 26.5px;
    color: var(--ink-light);
  }
  .contacts li {
    display: flex;
    justify-content: flex-end;
    align-items: center;
    gap: 4px;
  }
  .contacts svg {
    width: 18px;
    height: 18px;
    flex: none;
  }
</style>
</head>
<body>

<section class="card card--front" aria-label="Business card front">
  <svg class="card__shape" viewBox="0 0 800 455" preserveAspectRatio="none" aria-hidden="true">
    <path d="M308 0 C440 120 505 265 336 455 H330 C495 265 432 120 300 0 Z" fill="var(--paper)"/>
    <path d="M300 0 C432 120 495 265 330 455 H318 C474 265 420 120 292 0 Z" fill="var(--brand-yellow)"/>
    <path d="M0 0 H292 C420 120 474 265 318 455 H0 Z" fill="var(--paper)"/>
  </svg>

  <p class="wordmark">BrindleStaffing</p>

  <div class="person">
    <p class="person__name">Gordon Pratley</p>
    <p class="person__title">Chairman</p>
  </div>

  <address class="address">
    417 39th Avenue South<br>
    SAINT PETERSBURG FL 33712
  </address>

  <ul class="contacts">
    <li>813-555-4172
      <svg viewBox="0 0 18 18" aria-label="Mobile"><rect x="5" y="1" width="8" height="16" rx="1.5" fill="none" stroke="#fff" stroke-width="1.5"/><circle cx="9" cy="14.5" r="0.9" fill="#fff"/></svg>
    </li>
    <li>813-555-8036
      <svg viewBox="0 0 18 18" aria-label="Fax"><rect x="5" y="3" width="8" height="5" fill="#fff"/><rect x="2" y="8" width="14" height="7" rx="1" fill="#fff"/><rect x="5" y="11" width="8" height="2" fill="var(--brand-orange)"/></svg>
    </li>
    <li>gpratley@brindlestaffing.com
      <svg viewBox="0 0 18 18" aria-label="Email"><rect x="2" y="4" width="14" height="10" fill="#fff"/><path d="M2 4 L9 10 L16 4" fill="none" stroke="var(--brand-orange)" stroke-width="1.2"/></svg>
    </li>
    <li>www.brindlestaffing.com
      <svg viewBox="0 0 18 18" aria-label="Website"><circle cx="9" cy="9" r="7.5" fill="#fff"/><ellipse cx="9" cy="9" rx="3" ry="7.5" fill="none" stroke="var(--brand-orange)" stroke-width="1"/><path d="M1.5 9 H16.5" stroke="var(--brand-orange)" stroke-width="1"/></svg>
    </li>
  </ul>
</section>

<section class="card card--back" aria-label="Business card back">
  <p class="wordmark">BrindleStaffing</p>
</section>

</body>
</html>
```